Business Card Design

I am a realtor and i also flip houses. I am CEO and Founder of my business which is Voskell Group LLC which is named after my great uncle who died and i was really close to. He was a wonderful friendly man so i want my business to represent him too. My business works with a lot of different people but i want mainly something to show i am a strong confidant woman who owns there own business. I have a really fun personality so i don't want anything TOO serious or manly. I want the perfect mix. My last two business cards i created are too embarrassing to hand out because they are far too girly and i deal with a lot of millionaire clients. I live out in the Palm Springs California area. I think its very important to show i am a single mom, female with her own business at only 24. I don't want to just be a female that blends in with all of the other serious people but yet i don't want to seem immature. People are telling me to stay away from pinks and purples but i don't want blues and greens because they represent men more. But i won't say no to them if there is a happy medium.

Industry/Entity Type

Realtor

Contact Information for Business Card

Voskell Group, LLC
Corinne Tabb
27358 Halvern Ave, C2 517
Mesa Alondra, CA 92418
760-419-6735
Corinnedtabb@mailvane.com

```html
<!DOCTYPE html>
<html lang="en">
<head>
<meta charset="utf-8">
<title>Voskell Group LLC – Business Card</title>
<link rel="stylesheet" href="https://fonts.googleapis.com/css2?family=Nova+Square&display=swap">
<style>
  :root {
    --pink: #f2b0d4;
    --mauve: #a59fb4;
    --teal: #338a94;
    --yellow: #f9f97c;
    --card-w: 1200px;
    --card-h: 702px;
  }
  * { margin: 0; padding: 0; box-sizing: border-box; }
  html, body {
    width: var(--card-w);
    height: var(--card-h);
    overflow: hidden;
  }
  .business-card {
    position: relative;
    width: var(--card-w);
    height: var(--card-h);
    background: linear-gradient(90deg, var(--pink) 0%, var(--mauve) 17%, var(--teal) 46%, var(--teal) 100%);
    font-family: "Nova Square", sans-serif;
    font-weight: 400;
    color: var(--yellow);
    overflow: hidden;
  }
  .accent-stripes {
    position: absolute;
    inset: 0;
    width: 100%;
    height: 100%;
  }
  .accent-stripes polygon { fill: var(--yellow); }
  .company-name {
    position: absolute;
    left: 67px;
    top: 328px;
    font-size: 44px;
    white-space: nowrap;
  }
  .agent-name {
    position: absolute;
    left: 644px;
    top: 210px;
    font-size: 54px;
    font-weight: 400;
    letter-spacing: 1px;
    white-space: nowrap;
  }
  .address {
    position: absolute;
    left: 647px;
    top: 302px;
    font-size: 34px;
    line-height: 63px;
    font-style: normal;
    white-space: nowrap;
  }
  .contact-line {
    position: absolute;
    display: flex;
    align-items: center;
    white-space: nowrap;
  }
  .contact-line svg { flex: none; }
  .contact-line svg path { fill: var(--yellow); }
  .contact-phone { left: 317px; top: 537px; font-size: 36px; }
  .contact-phone svg { margin-right: 32px; }
  .contact-email { left: 314px; top: 606px; font-size: 33px; }
  .contact-email svg { margin-right: 40px; }
</style>
</head>
<body>
  <main class="business-card">
    <svg class="accent-stripes" viewBox="0 0 1200 702" aria-hidden="true">
      <polygon points="0,176 183,0 228,0 0,230"/>
      <polygon points="922,702 1200,433 1200,488 978,702"/>
    </svg>

    <p class="company-name">Voskell Group LLC</p>

    <h1 class="agent-name">Corinne Tabb</h1>
    <address class="address">
      27358 Halvern Ave<br>
      C2 517 Mesa Alondra<br>
      CA 92418
    </address>

    <p class="contact-line contact-phone">
      <svg width="42" height="42" viewBox="0 0 24 24" aria-hidden="true">
        <path d="M6.6 10.8c1.4 2.8 3.8 5.2 6.6 6.6l2.2-2.2c.3-.3.7-.4 1-.2 1.1.4 2.3.6 3.6.6.6 0 1 .4 1 1V20c0 .6-.4 1-1 1C10.6 21 3 13.4 3 4c0-.6.4-1 1-1h3.5c.6 0 1 .4 1 1 0 1.3.2 2.5.6 3.6.1.3 0 .7-.2 1L6.6 10.8z"/>
      </svg>
      <span>760-419-6735</span>
    </p>

    <p class="contact-line contact-email">
      <svg width="46" height="34" viewBox="0 0 46 34" aria-hidden="true">
        <path d="M0 0h46v34H0z M4 4v1.5l19 14 19-14V4z M4 10.5V30h38V10.5L23 24.5z" fill-rule="evenodd"/>
      </svg>
      <span>corinnedtabb@mailvane.com</span>
    </p>
  </main>
</body>
</html>
```